Business Card Design

Please copy the format of the attached card.

FRONT:
White text small blue horses head logo where "mivar" in in example

BACK:
Blue background w/ white horses head

Industry/Entity Type

Business

Contact Information for Business Card

Colby Marsh
Chief Executive Officer
Tundrel Inns & Resorts
417 Fenwick Street | San Francisco, California 94327
Tel: +1.415.772.3841
email: colby@tundrelinns.com

```html
<!DOCTYPE html>
<html lang="en">
<head>
<meta charset="utf-8">
<title>Tundrel Inns &amp; Resorts — Business Card</title>
<link href="https://fonts.googleapis.com/css2?family=Arimo:wght@400&display=swap" rel="stylesheet">
<style>
  :root {
    --backdrop: #2b2b2b;
    --card-white: #ffffff;
    --brand-blue: #1f3f7a;
    --ink-dark: #2a2a2a;
    --ink-white: #ffffff;
    --font-main: "Arimo", Arial, sans-serif;
  }
  * { box-sizing: border-box; margin: 0; padding: 0; }
  html, body {
    width: 1200px;
    height: 900px;
    overflow: hidden;
    background: var(--backdrop);
    font-family: var(--font-main);
  }
  .canvas {
    position: relative;
    width: 1200px;
    height: 900px;
  }
  .card {
    position: absolute;
    width: 560px;
    height: 320px;
    box-shadow: 0 10px 30px rgba(0,0,0,0.45);
  }

  /* Front card */
  .card--front {
    left: 150px;
    top: 100px;
    background: var(--card-white);
    padding: 56px 48px;
    color: var(--ink-dark);
  }
  .brand-mark {
    display: flex;
    align-items: center;
    gap: 10px;
    font-size: 22px;
    line-height: 1;
  }
  .brand-mark__dot {
    width: 16px;
    height: 16px;
    border-radius: 50%;
    background: currentColor;
  }
  .card--front .brand-mark { color: var(--brand-blue); }
  .holder {
    margin-top: 40px;
    display: flex;
    align-items: baseline;
    gap: 6px;
  }
  .holder__name {
    font-size: 24px;
    color: var(--brand-blue);
  }
  .holder__title {
    font-size: 13px;
    color: var(--ink-dark);
  }
  .details {
    margin-top: 8px;
    font-size: 14px;
    line-height: 1.3;
  }
  .details__company { color: var(--brand-blue); }
  .contact {
    margin-top: 14px;
    font-size: 14px;
    line-height: 1.3;
  }
  .contact__label { color: var(--brand-blue); }

  /* Back card */
  .card--back {
    left: 490px;
    top: 470px;
    background: var(--brand-blue);
    color: var(--ink-white);
    display: flex;
    flex-direction: column;
    align-items: center;
    justify-content: center;
    text-align: center;
  }
  .card--back .brand-mark {
    font-size: 26px;
    color: var(--ink-white);
  }
  .back__company {
    margin-top: 22px;
    font-size: 32px;
  }
  .back__web {
    margin-top: 30px;
    font-size: 13px;
    letter-spacing: 4px;
  }
</style>
</head>
<body>
<main class="canvas">
  <section class="card card--front" aria-label="Card front">
    <div class="brand-mark"><span class="brand-mark__dot"></span><span>Tundrel</span></div>
    <div class="holder">
      <span class="holder__name">Colby Marsh</span>
      <span class="holder__title">| Chief Executive Officer</span>
    </div>
    <div class="details">
      <div class="details__company">Tundrel Inns &amp; Resorts</div>
      <div>417 Fenwick Street | San Francisco, California 94327</div>
    </div>
    <div class="contact">
      <div><span class="contact__label">tel:</span> +1.415.772.3841</div>
      <div><span class="contact__label">email:</span> colby@tundrelinns.com</div>
    </div>
  </section>

  <section class="card card--back" aria-label="Card back">
    <div class="brand-mark"><span class="brand-mark__dot"></span><span>Tundrel</span></div>
    <div class="back__company">Tundrel Inns &amp; Resorts</div>
    <div class="back__web">www.tundrelinns.com</div>
  </section>
</main>
</body>
</html>
```